High Tech Real Estate Startup needs a business card

We are developing an innovative real estate marketing product based around advanced search and virtual reality.

We talk to people, we need business cards.

Target Market(s)

The target market is technology professionals and realtors.

Contact Information for Business Card

The information to be included will include

Name
Title
Phone Number
E-mail Address
www.zelquin.com

It should use simple iconography for each one of those fields.

Font styles to use
Other font styles liked:
• Co, Jubilat, Avenir

Colors

Designer to choose colors to be used in the design.

Requirements
Must have
• Clean aesthetic,
• Good use of negative space.
• It should use our company logo, shown in the attached file. It is able to use the negative of that logo (coloured font and white background) and I have attached other acceptable accent colours in a swatch file.
Should not have
• Should not be too busy
• No extraneous text (slogans, tag lines etc)

```html
<!DOCTYPE html>
<html lang="en">
<head>
<meta charset="utf-8">
<title>Zelquin Business Card</title>
<link rel="stylesheet" href="https://fonts.googleapis.com/css2?family=Mulish:wght@400;600&display=swap">
<style>
  :root {
    --teal: #12b4b9;
    --ink: #48606c;
    --paper: #ffffff;
    --backdrop: #ecebe7;
  }
  * { margin: 0; padding: 0; box-sizing: border-box; }
  html, body { width: 1200px; height: 1000px; overflow: hidden; }
  body {
    background: var(--backdrop);
    font-family: "Mulish", "Avenir", sans-serif;
    color: var(--ink);
    position: relative;
  }
  .card {
    position: absolute;
    background: var(--paper);
    box-shadow: 0 4px 14px rgba(0,0,0,0.12);
    overflow: hidden;
  }
  .card-front { left: 270px; top: 78px; width: 658px; height: 375px; }
  .card-back { left: 270px; top: 534px; width: 660px; height: 376px; }

  .wordmark {
    color: var(--teal);
    font-weight: 600;
    letter-spacing: 1px;
    line-height: 1;
  }
  .card-front .wordmark {
    position: absolute;
    left: 0; right: 0; top: 150px;
    text-align: center;
    font-size: 72px;
  }

  .person-name {
    position: absolute; left: 48px; top: 124px;
    font-size: 33px; font-weight: 400; line-height: 1;
  }
  .person-title {
    position: absolute; left: 50px; top: 170px;
    font-size: 18px; line-height: 1;
  }
  .title-rule {
    position: absolute; left: 200px; top: 183px;
    width: 422px; height: 2px; background: var(--ink);
  }
  .contact-list { position: absolute; left: 48px; top: 248px; list-style: none; }
  .contact-item {
    display: flex; align-items: center;
    height: 36px; font-size: 21px;
  }
  .contact-item svg { width: 18px; height: 18px; margin-right: 22px; fill: var(--ink); }

  .card-back .wordmark {
    position: absolute; right: 38px; top: 268px;
    font-size: 44px;
  }
  .web-band { position: absolute; right: 0; bottom: 0; width: 290px; height: 62px; }
  .web-address {
    position: absolute; right: 38px; bottom: 20px;
    color: var(--paper); font-size: 19px; letter-spacing: 0.5px; line-height: 1;
  }
</style>
</head>
<body>
  <section class="card card-front">
    <div class="wordmark">ZELQUIN</div>
  </section>

  <section class="card card-back">
    <h1 class="person-name">Name of Person</h1>
    <p class="person-title">Title of Person</p>
    <div class="title-rule"></div>

    <ul class="contact-list">
      <li class="contact-item">
        <svg viewBox="0 0 24 24" aria-hidden="true"><path d="M6.6 10.8a15.1 15.1 0 0 0 6.6 6.6l2.2-2.2a1 1 0 0 1 1-.25 11.4 11.4 0 0 0 3.6.57 1 1 0 0 1 1 1V20a1 1 0 0 1-1 1A17 17 0 0 1 3 4a1 1 0 0 1 1-1h3.5a1 1 0 0 1 1 1c0 1.25.2 2.45.57 3.57a1 1 0 0 1-.25 1z"/></svg>
        <span>+123 456 7890</span>
      </li>
      <li class="contact-item">
        <svg viewBox="0 0 24 24" aria-hidden="true"><path d="M2 5h20v14H2z" fill="none"/><path d="M2 6l10 7 10-7V5H2zM2 8.4V19h20V8.4l-10 7z"/></svg>
        <span>E-mail Address</span>
      </li>
    </ul>

    <div class="wordmark">ZELQUIN</div>

    <svg class="web-band" viewBox="0 0 290 62" aria-hidden="true">
      <path d="M0 62 L20 16 Q27 0 48 0 L290 0 L290 62 Z" fill="var(--teal)"/>
    </svg>
    <p class="web-address">www.zelquin.com</p>
  </section>
</body>
</html>
```